Builder of high-end, expensive tables and other furniture

Build a website that represents what we do. I want a luxury feel that appeals to those who can afford our products. We build very high end tables and other furniture using trees that have fallen or are standing dead. We never cut living trees. Trees are harvested, milled, and kiln dried. Then that lumber is meticulously turned into fine furniture using the best equipment. Our furniture prices range from $1,000-$20,000.

Trying to figure out how to raise my spend.

```html
<!DOCTYPE html>
<html lang="en">
<head>
<meta charset="utf-8">
<title>Fallen Oak Tables — Fine Furniture from Fallen Timber</title>
<link rel="stylesheet" href="https://fonts.googleapis.com/css2?family=Marcellus&family=Roboto:wght@400;500;700&display=swap">
<style>
:root{
  --orange:#f47a2e;
  --orange-light:#ff9448;
  --blue:#1b5c97;
  --blue-accent:#3a8fd6;
  --blue-light:#5aaee8;
  --ink:#111;
  --text:#555;
  --muted:#666;
  --blush:#fdf1ee;
  --white:#fff;
  --footer:#050505;
}
*{box-sizing:border-box;margin:0;padding:0}
html,body{width:1200px;height:4219px;overflow:hidden}
body{font-family:'Roboto',sans-serif;color:var(--text);background:var(--white);position:relative}
.abs{position:absolute}
.heading{font-family:'Marcellus',serif;color:var(--ink);font-weight:400}
.center{left:0;width:1200px;text-align:center}
.rule{width:58px;height:5px;border-radius:3px;background:var(--blue-accent)}
.btn{display:inline-block;background:linear-gradient(180deg,var(--orange-light),var(--orange));color:#fff;font-weight:700;font-size:15px;border-radius:22px;height:42px;line-height:42px;padding:0 24px;text-decoration:none;box-shadow:0 4px 10px rgba(244,122,46,.25)}
.brand{font-family:'Marcellus',serif;color:var(--orange);white-space:nowrap;display:flex;align-items:center;gap:8px}
.brand .dot{width:12px;height:12px;border-radius:50%;background:var(--orange)}

/* header */
.top-bar{top:0;left:0;width:1200px;height:5px;background:var(--orange)}
.socials{display:flex;gap:12px}
.soc{width:43px;height:43px;border-radius:50%;border:1.5px solid var(--blue);display:flex;align-items:center;justify-content:center}
.soc.filled{background:var(--blue)}
.soc span{width:10px;height:10px;border-radius:50%;background:var(--blue)}
.soc.filled span{background:#fff}
.phone{top:43px;left:878px;display:flex;align-items:center;gap:14px}
.phone .ic{width:42px;height:42px;border-radius:50%;background:var(--blue);display:flex;align-items:center;justify-content:center}
.phone small{display:block;font-size:11px;color:var(--blue)}
.phone strong{font-size:18px;color:var(--ink);font-weight:500}
.nav{top:138px;left:0;width:1200px;display:flex;justify-content:center;gap:0}
.nav a{font-size:14px;color:var(--ink);text-decoration:none;font-weight:500;padding:0 34px}
.header-line{top:186px;left:0;width:1200px;height:1px;background:#eee}

/* hero */
.hero{top:187px;left:0;width:1200px;height:600px;background:linear-gradient(180deg,#f2f1ef 0%,#e9e7e4 70%,#cfc3b5 88%,#b7a592 100%)}
.hero-title{top:300px;left:112px;font-size:50px}
.hero-brand{top:410px;left:112px;font-size:68px}
.hero-text{top:510px;left:112px;width:520px;font-size:16.5px;line-height:29px;color:#333}
.hero-btn{top:616px;left:111px}

/* what we do */
.wwd-title{top:895px;font-size:50px}
.para{font-size:13.5px;line-height:30px;color:var(--muted)}
.card{width:297px;height:298px;border-radius:6px;box-shadow:0 3px 14px rgba(0,0,0,.08);background:#fff;overflow:hidden}
.card .ph{width:100%;height:100%}
.feat{display:flex;align-items:center;gap:26px;font-size:13.5px;color:var(--muted)}

/* about */
.about{top:1771px;left:0;width:1200px;height:470px;background:linear-gradient(90deg,#ebe4da 0%,#efe9e1 55%,#ece5dc 100%)}
.about-floor{top:2180px;left:0;width:1200px;height:61px;background:linear-gradient(180deg,#e4dbcf,#d9cebf)}

/* how */
.step{width:332px;text-align:center}
.step h3{font-family:'Marcellus',serif;font-weight:400;color:var(--ink);font-size:31px;margin-top:0}
.step p{font-size:13.5px;line-height:24px;color:var(--muted);margin-top:14px;padding:0 28px}
.diamond-wrap{width:230px;height:230px;margin:0 auto 14px;position:relative}

/* products */
.products{top:3115px;left:0;width:1200px;height:714px;background:var(--blush)}
.prod{width:222px;text-align:center}
.prod .ph{height:262px;background:#fff}
.prod .name{margin-top:30px;font-size:16px;color:#333}
.prod .price{margin-top:10px;font-size:15px;color:var(--ink);font-weight:700}

/* footer */
.footer{top:3829px;left:0;width:1200px;height:390px;background:var(--footer)}
.fnav{display:flex;justify-content:center;gap:0}
.fnav a{color:#fff;text-decoration:none;font-size:14px;font-weight:700;padding:0 38px}
.pay{display:flex;gap:8px;justify-content:center}
.pay span{width:68px;height:38px;background:#fff;border-radius:3px;display:flex;align-items:center;justify-content:center}
.pay span i{display:block;width:34px;height:10px;border-radius:2px;background:#c8ccd3}
.copy{font-size:12px;color:#fff}
.fsoc{display:flex;gap:12px;justify-content:center}
.fsoc span{width:30px;height:30px;border-radius:50%;border:1.5px solid var(--orange);display:flex;align-items:center;justify-content:center}
.fsoc span:first-child{background:var(--orange)}
.fsoc span i{width:8px;height:8px;border-radius:50%;background:var(--orange)}
.fsoc span:first-child i{background:#fff}
</style>
</head>
<body>

<!-- Header -->
<div class="abs top-bar"></div>
<div class="abs socials" style="top:44px;left:111px">
  <div class="soc filled" aria-label="Social link"><span></span></div>
  <div class="soc" aria-label="Social link"><span></span></div>
  <div class="soc" aria-label="Social link"><span></span></div>
</div>
<div class="abs brand" style="top:48px;left:0;width:1200px;justify-content:center;font-size:34px"><span class="dot"></span>Fallen Oak Tables</div>
<div class="abs phone">
  <div class="ic"><svg width="18" height="18" viewBox="0 0 24 24"><path fill="#fff" d="M6.6 10.8a15 15 0 0 0 6.6 6.6l2.2-2.2c.3-.3.7-.4 1-.2 1.1.4 2.3.6 3.6.6.6 0 1 .4 1 1V20c0 .6-.4 1-1 1A17 17 0 0 1 3 4c0-.6.4-1 1-1h3.5c.6 0 1 .4 1 1 0 1.3.2 2.5.6 3.6.1.3 0 .7-.2 1z"/></svg></div>
  <div><small>Call Us:</small><strong>+1 555 0142 7788</strong></div>
</div>
<nav class="abs nav">
  <a href="#">Home</a><a href="#">About Us</a><a href="#">How It Works</a><a href="#">Services</a><a href="#">Shop</a><a href="#">Testimonials</a><a href="#">Contact Us</a>
</nav>
<div class="abs header-line"></div>

<!-- Hero -->
<section class="abs hero" role="img" aria-label="Bright living room with a navy velvet armchair, side table with vases and dried branches, wall clock and pendant lamps"></section>
<h1 class="abs heading hero-title">Welcome To</h1>
<div class="abs brand hero-brand"><span class="dot" style="width:20px;height:20px"></span>Fallen Oak Tables</div>
<p class="abs hero-text">Lorem ipsum dolor sit amet, consectetur adipiscing elit, sed do eiusmod tempor incididunt ut labore et dolore magna aliqua. Ut enim ad minim veniam, quis nostrud</p>
<a class="abs btn hero-btn" href="#">Get Started Now</a>

<!-- What We Do -->
<h2 class="abs heading center wwd-title">What We Do</h2>
<div class="abs rule" style="top:973px;left:571px"></div>
<p class="abs para center" style="top:1013px;left:160px;width:880px">Sed ut perspiciatis unde omnis iste natus error sit voluptatem accusantium doloremque laudantium, totam rem aperiam, eaque ipsa quae ab illo inventore veritatis et quasi architecto beatae vitae dicta sunt explicabo. Nemo enim ipsam voluptatem quia voluptas sit aspernatur aut odit aut fugit, sed quia consequuntur magni dolores eos qui ratione voluptatem sequi nesciunt. Neque porro quisquam est, qui dolorem ipsum quia dolor sit amet, consectetur, adipisci velit, sed quia non numquam eius modi</p>

<div class="abs card" style="top:1182px;left:111px"><div class="ph" role="img" aria-label="Round walnut pedestal table on white" style="background:radial-gradient(ellipse at 50% 40%,#c99a6c 0,#b07d4f 22%,#fff 46%)"></div></div>
<div class="abs card" style="top:1182px;left:452px"><div class="ph" role="img" aria-label="Light wood sideboard with rattan rug and plant" style="background:linear-gradient(180deg,#eeece8 0%,#e6e1d9 55%,#cdb896 75%,#e8e3dc 100%)"></div></div>
<div class="abs card" style="top:1182px;left:792px"><div class="ph" role="img" aria-label="Cherry wood dining table with upholstered chairs" style="background:linear-gradient(180deg,#d9cdbd 0%,#9a5a2f 45%,#6e3518 75%,#8c4a24 100%)"></div></div>

<div class="abs feat" style="top:1512px;left:193px">
  <svg width="30" height="42" viewBox="0 0 30 42" fill="none" stroke="#333" stroke-width="1.6"><path d="M8 4c0-2 14-2 14 0v16H8z"/><path d="M5 22h20v5H5zM7 27l-2 13M23 27l2 13M11 27v10M19 27v10"/></svg>
  <span>Table Chair</span>
</div>
<div class="abs feat" style="top:1516px;left:522px">
  <svg width="56" height="34" viewBox="0 0 56 34" fill="none" stroke="#333" stroke-width="1.6"><path d="M15 8h26v4H15zM20 12v20M36 12v20"/><path d="M2 4v22h10v6M12 18H2M54 4v22H44v6M44 18h10"/></svg>
  <span>Table Chair</span>
</div>
<div class="abs feat" style="top:1512px;left:870px"><svg width="40" height="44" viewBox="0 0 40 44" fill="none" stroke="#333" stroke-width="1.6"><path d="M6 2h28v14H6zM3 18h34v5H3zM8 23l24 19M32 23 8 42M6 42h8M26 42h8"/></svg>
  <span>Table Chair</span>
</div>
<a class="abs btn" href="#" style="top:1616px;left:518px">Get Started Now</a>

<!-- About -->
<section class="abs about" role="img" aria-label="Calm room with a tan armchair, wooden sideboard, lamp, vase of branches and hanging copper bulbs"></section>
<div class="abs about-floor" aria-hidden="true"></div>
<h2 class="abs heading" style="top:1846px;left:704px;font-size:50px">About Us</h2>
<div class="abs rule" style="top:1923px;left:704px"></div>
<p class="abs" style="top:1954px;left:703px;width:390px;font-size:13.5px;line-height:26px;color:var(--muted)">Lorem ipsum dolor sit amet, consectetur adipiscing elit, sed do eiusmod tempor incididunt ut labore et dolore magna aliqua. Quis ipsum suspendisse ultrices gravida. Risus commodo viverra maecenas accumsan lacus vel facilisis.Sed ut perspiciatis unde omnis iste natus</p>
<a class="abs btn" href="#" style="top:2110px;left:703px">Read More</a>

<!-- How It Works -->
<h2 class="abs heading center" style="top:2333px;font-size:50px">How It Works</h2>
<div class="abs rule" style="top:2411px;left:571px"></div>
<p class="abs para center" style="top:2442px;left:170px;width:860px">Sed ut perspiciatis unde omnis iste natus error sit voluptatem accusantium doloremque laudantium, totam rem aperiam, eaque ipsa quae ab illo inventore veritatis et quasi architecto beatae vitae dicta sunt explicabo. Nemo enim ipsam voluptatem quia</p>

<div class="abs step" style="top:2573px;left:101px">
  <div class="diamond-wrap">
    <svg width="230" height="230" viewBox="0 0 230 230">
      <defs><linearGradient id="gBlue" x1="0" y1="0" x2="0" y2="1"><stop offset="0" stop-color="#6cc0f2"/><stop offset="1" stop-color="#2d6fb0"/></linearGradient></defs>
      <rect x="48" y="48" width="134" height="134" rx="16" transform="rotate(45 115 115)" fill="url(#gBlue)"/>
      <rect x="35" y="35" width="160" height="160" rx="12" fill="#fff" style="filter:drop-shadow(0 3px 8px rgba(0,0,0,.12))"/>
      <g fill="none" stroke="#2d6fb0" stroke-width="2.2"><circle cx="95" cy="108" r="13"/><circle cx="117" cy="100" r="15"/><circle cx="138" cy="110" r="12"/><path d="M95 121v18M117 115v24M138 122v17M80 139h70"/></g>
    </svg>
  </div>
  <h3>Harvested</h3>
  <p>Lorem ipsum dolor sit amet, consectetur adipiscing elit, sed do eiusmod tempor incididunt ut labore et dolore</p>
</div>
<div class="abs step" style="top:2573px;left:433px">
  <div class="diamond-wrap">
    <svg width="230" height="230" viewBox="0 0 230 230">
      <defs><linearGradient id="gOr" x1="0" y1="0" x2="0" y2="1"><stop offset="0" stop-color="#ff6b2a"/><stop offset="1" stop-color="#ff9a45"/></linearGradient></defs>
      <rect x="48" y="48" width="134" height="134" rx="16" transform="rotate(45 115 115)" fill="url(#gOr)"/>
      <rect x="35" y="35" width="160" height="160" rx="12" fill="#fff" style="filter:drop-shadow(0 3px 8px rgba(0,0,0,.12))"/>
      <g fill="none" stroke="#f47a2e" stroke-width="2.2"><circle cx="104" cy="120" r="18" stroke-dasharray="6 4"/><circle cx="104" cy="120" r="7"/><path d="M112 88h30v10h-30zM118 98l4 14h10l4-14"/></g>
    </svg>
  </div>
  <h3>Milled</h3>
  <p>Lorem ipsum dolor sit amet, consectetur adipiscing elit, sed do eiusmod tempor incididunt ut labore et dolore</p>
</div>
<div class="abs step" style="top:2573px;left:765px">
  <div class="diamond-wrap">
    <svg width="230" height="230" viewBox="0 0 230 230">
      <rect x="48" y="48" width="134" height="134" rx="16" transform="rotate(45 115 115)" fill="url(#gBlue)"/>
      <rect x="35" y="35" width="160" height="160" rx="12" fill="#fff" style="filter:drop-shadow(0 3px 8px rgba(0,0,0,.12))"/>
      <g fill="none" stroke="#2d6fb0" stroke-width="2.2"><rect x="82" y="86" width="66" height="58" rx="3"/><path d="M82 96h66M138 96v48"/><path d="M110 134c-8 0-10-10-2-18 0 6 4 6 6 2 6 6 4 16-4 16z"/></g>
    </svg>
  </div>
  <h3>Kiln Dried</h3>
  <p>Lorem ipsum dolor sit amet, consectetur adipiscing elit, sed do eiusmod tempor incididunt ut labore et dolore</p>
</div>
<a class="abs btn" href="#" style="top:2984px;left:531px">Get Started</a>

<!-- Products -->
<section class="abs products"></section>
<h2 class="abs heading center" style="top:3190px;font-size:50px">Our Products</h2>
<div class="abs rule" style="top:3268px;left:571px"></div>
<p class="abs para center" style="top:3300px;left:170px;width:860px">Sed ut perspiciatis unde omnis iste natus error sit voluptatem accusantium doloremque laudantium, totam rem aperiam, eaque ipsa quae ab illo inventore veritatis et quasi architecto beatae vitae dicta sunt explicabo. Nemo enim ipsam voluptatem quia</p>

<div class="abs prod" style="top:3408px;left:103px">
  <div class="ph" role="img" aria-label="Light oak wooden chair" style="background:radial-gradient(ellipse at 50% 50%,#d9a56b 0,#e6c29a 18%,#fff 42%)"></div>
  <div class="name">Wooden Chair</div><div class="price">$1,000</div>
</div>
<div class="abs prod" style="top:3408px;left:360px">
  <div class="ph" role="img" aria-label="Round mahogany pedestal table" style="background:radial-gradient(ellipse at 50% 45%,#7a3a1e 0,#93502c 20%,#fff 44%)"></div>
  <div class="name">Wooden Chair</div><div class="price">$1,200</div>
</div>
<div class="abs prod" style="top:3408px;left:618px">
  <div class="ph" role="img" aria-label="Round light wood side table" style="background:radial-gradient(ellipse at 50% 45%,#e0b784 0,#ecd0a8 20%,#fff 44%)"></div>
  <div class="name">Wooden Chair</div><div class="price">$1,500</div>
</div>
<div class="abs prod" style="top:3408px;left:876px">
  <div class="ph" role="img" aria-label="Black metal chair with wooden seat" style="background:radial-gradient(ellipse at 50% 50%,#2a2a2a 0,#6b5a48 16%,#fff 42%)"></div>
  <div class="name">Wooden Chair</div><div class="price">$2,000</div>
</div>

<!-- Footer -->
<footer class="abs footer"></footer>
<div class="abs brand" style="top:3914px;left:0;width:1200px;justify-content:center;font-size:34px"><span class="dot"></span>Fallen Oak Tables</div>
<nav class="abs fnav" style="top:4002px;left:0;width:1200px">
  <a href="#">Home</a><a href="#">How It Works</a><a href="#">Services</a><a href="#">Shop</a><a href="#">Testimonials</a><a href="#">Contact Us</a>
</nav>
<div class="abs pay" style="top:4054px;left:0;width:1200px" aria-label="Accepted payment methods">
  <span><i></i></span><span><i></i></span><span><i></i></span><span><i></i></span><span><i></i></span>
</div>
<p class="abs copy center" style="top:4120px">© Copyright 2023 Fallen Oak Tables | All Rights Reserved.</p>
<div class="abs fsoc" style="top:4158px;left:0;width:1200px">
  <span><i></i></span><span><i></i></span><span><i></i></span>
</div>

</body>
</html>
```